Professional Package for CPA Firm

We would like a stationery design for our new CPA Firm based in Atlanta, GA called 'Vale 8'. We work with investors to help grow investments, tax free. We would like the design to have a professional/minimal look with a 'wow' factor. We need 9.5″ x 4.125″, 9x12, and 10x13 mailing envelopes, business cards, and a letterhead. We have a logo that is already complete. For the letterhead, we would like to have space to put credentials at the bottom of the page

Industry/Entity Type

CPA, Accounting

```html
<!DOCTYPE html>
<html lang="en">
<head>
<meta charset="utf-8">
<title>Vale 8 Stationery</title>
<link href="https://fonts.googleapis.com/css2?family=Montserrat:wght@400;500;700&family=Arimo:wght@400;700&display=swap" rel="stylesheet">
<style>
:root{
  --navy:#0b2f3c;
  --card-dark:#022e3d;
  --teal:#23a0ae;
  --red:#f0414b;
  --ink:#555e63;
  --muted:#9aa0a4;
  --stage:#aaaaaa;
  --paper:#ffffff;
  --paper-shade:#ececec;
}
*{box-sizing:border-box;margin:0;padding:0}
html,body{width:849px;height:1200px;overflow:hidden;background:var(--stage)}
.canvas{position:relative;width:849px;height:1200px;font-family:"Montserrat",sans-serif}
.piece{position:absolute;background:linear-gradient(90deg,var(--paper-shade),var(--paper) 70%);box-shadow:2px 3px 4px rgba(0,0,0,.28);overflow:hidden}
.abs{position:absolute;white-space:nowrap}
.brand-name{font-family:"Montserrat",sans-serif;font-weight:700;color:var(--navy);letter-spacing:.02em;line-height:1}
.brand-tag{font-family:"Montserrat",sans-serif;font-weight:500;color:var(--navy);line-height:1}
.small-addr{font-family:"Arimo",sans-serif;color:var(--ink);line-height:1.25}

/* business card front */
.card-front{left:123px;top:32px;width:289px;height:165px;background:var(--paper)}
.card-front .brand-name{left:40px;top:101px;font-size:24px}
.card-front .brand-tag{left:41px;top:122px;font-size:7.6px}
.card-divider{left:144px;top:38px;width:1px;height:89px;background:#c9cccf}
.card-info{left:157px;top:39px;font-family:"Arimo",sans-serif;color:var(--ink);font-size:8px;line-height:1.2}
.card-info .person{color:var(--red);font-weight:700;font-size:10px}
.card-info .role{margin-bottom:9px}
.card-info .addr{margin-bottom:8px}
.contact-row{display:flex;align-items:center;gap:4px;height:11.5px}
.contact-row svg{width:6px;height:6px;flex:none}

/* business card back */
.card-back{left:452px;top:32px;width:289px;height:165px;background:var(--card-dark)}
.card-back .brand-name{left:0;right:0;top:101px;font-size:25px;color:#fff;text-align:center}
.card-back .brand-tag{left:0;right:0;top:124px;font-size:8px;color:#fff;text-align:center}

/* letterhead */
.letterhead{left:37px;top:225px;width:379px;height:535px}
.letterhead .brand-name{left:25px;top:47px;font-size:13px}
.letterhead .brand-tag{left:25px;top:60px;font-size:3.8px}
.lh-contact{left:284px;top:18px;font-size:5.5px;line-height:1.45}
.lh-contact .gap{height:4px}
.lh-contact .contact-row{height:9px;gap:3px}
.lh-contact .contact-row svg{width:4.5px;height:4.5px}
.lh-rule{left:25px;top:66px;width:328px;height:1px;background:#9aa0a4}
.lh-to{left:38px;top:119px;font-size:6.5px;letter-spacing:.15em;color:var(--navy)}
.lh-date{right:39px;top:119px;font-size:5px;color:var(--ink)}
.lh-recipient{left:38px;top:130px;font-size:4.6px;line-height:1.85;color:var(--muted)}
.lh-recipient .to-name{color:var(--red);font-size:6px}
.lh-body{position:absolute;left:38px;top:192px;width:302px;font-size:4.7px;line-height:1.45;color:var(--muted);text-align:justify}
.lh-body p{margin-bottom:6.5px}
.lh-signature{left:38px;top:377px;width:64px;height:18px;background:linear-gradient(90deg,rgba(11,47,60,.18),rgba(11,47,60,.04));border-radius:2px}
.lh-signer{left:37px;top:399px;font-size:6px;color:var(--navy)}
.lh-signer-role{left:37px;top:408px;font-size:4.4px;color:var(--muted)}

/* envelopes with return address */
.env-large{left:456px;top:225px;width:354px;height:460px}
.env-large .brand-name{left:20px;top:55px;font-size:17px}
.env-large .brand-tag{left:20px;top:73px;font-size:5.2px}
.env-large .small-addr{left:20px;top:83px;font-size:5px}

.env-medium{left:456px;top:730px;width:336px;height:425px}
.env-medium .brand-name{left:18px;top:52px;font-size:17px}
.env-medium .brand-tag{left:18px;top:70px;font-size:5.2px}
.env-medium .small-addr{left:18px;top:80px;font-size:5px}

.env-business{left:28px;top:794px;width:387px;height:168px}
.env-business .brand-name{left:12px;top:37px;font-size:12px}
.env-business .brand-tag{left:12px;top:49px;font-size:3.6px}
.env-business .small-addr{left:12px;top:57px;font-size:5px}

.env-back{left:28px;top:987px;width:387px;height:168px}
.env-flap{position:absolute;left:0;top:0;width:387px;height:50px}
.env-back .brand-name{left:0;right:0;top:24px;font-size:9px;text-align:center}
.env-back .brand-tag{left:0;right:0;top:34px;font-size:2.6px;text-align:center}
</style>
</head>
<body>
<main class="canvas">

  <section class="piece card-front" aria-label="Business card front">
    <div class="abs brand-name">VALE 8</div>
    <div class="abs brand-tag">CPAS and Tax Advisors</div>
    <div class="abs card-divider"></div>
    <div class="abs card-info">
      <div class="person">DANIEL REYES</div>
      <div class="role">Manager</div>
      <div class="addr">Your address, city<br>state, ZIP 0000</div>
      <div class="contact-row"><svg viewBox="0 0 10 10"><path d="M2 1l2 2-1 1.5c.6 1.2 1.3 1.9 2.5 2.5L7 6l2 2-1.5 1.5C4 9 1 6 .5 2.5z" fill="var(--red)"/></svg>555-018-2400</div>
      <div class="contact-row"><svg viewBox="0 0 10 10"><rect x="0" y="2" width="10" height="6.5" fill="var(--red)"/><path d="M0 2l5 3.5L10 2" stroke="#fff" stroke-width="1" fill="none"/></svg>office@vale8cpa.com</div>
      <div class="contact-row"><svg viewBox="0 0 10 10"><circle cx="5" cy="5" r="4.6" fill="var(--red)"/><path d="M.5 5h9M5 .5v9" stroke="#fff" stroke-width=".8"/></svg>www.vale8cpa.com</div>
    </div>
  </section>

  <section class="piece card-back" aria-label="Business card back">
    <div class="abs brand-name">VALE 8</div>
    <div class="abs brand-tag">CPAS and Tax Advisors</div>
  </section>

  <section class="piece letterhead" aria-label="Letterhead">
    <div class="abs brand-name">VALE 8</div>
    <div class="abs brand-tag">CPAS and Tax Advisors</div>
    <div class="abs small-addr lh-contact">
      Your address, city<br>state, ZIP 0000
      <div class="gap"></div>
      <div class="contact-row"><svg viewBox="0 0 10 10"><path d="M2 1l2 2-1 1.5c.6 1.2 1.3 1.9 2.5 2.5L7 6l2 2-1.5 1.5C4 9 1 6 .5 2.5z" fill="var(--red)"/></svg>555-018-2400</div>
      <div class="contact-row"><svg viewBox="0 0 10 10"><rect x="0" y="2" width="10" height="6.5" fill="var(--red)"/><path d="M0 2l5 3.5L10 2" stroke="#fff" stroke-width="1" fill="none"/></svg>office@vale8cpa.com</div>
      <div class="contact-row"><svg viewBox="0 0 10 10"><circle cx="5" cy="5" r="4.6" fill="var(--red)"/><path d="M.5 5h9M5 .5v9" stroke="#fff" stroke-width=".8"/></svg>www.vale8cpa.com</div>
    </div>
    <div class="abs lh-rule"></div>
    <div class="abs lh-to">TO</div>
    <div class="abs lh-date">Friday, 01/01/2018</div>
    <div class="abs lh-recipient">
      <div class="to-name">Laura Pennick</div>
      Human Resources<br>Northfield Co.<br>214 Birch Lane, Elmwood<br>E89 USA
    </div>
    <div class="lh-body">
      <p>Lorem ipsum dolor sit amet, consectetuer adipiscing elit, sed diam nonummy nibh euismod tincidunt ut laoreet dolore magna aliquam erat volutpat. Ut wisi enim ad minim veniam, quis nostrud exerci tation ullamcorper suscipit lobortis nisl ut aliquip ex ea commodo consequat. Duis autem vel eum iriure dolor in hendrerit in vulputate velit esse molestie consequat, vel illum dolore eu feugiat nulla facilisis at vero eros et accumsan et iusto odio dignissim qui blandit praesent luptatum zzril delenit augue duis dolore te feugait nulla facilisi.</p>
      <p>Nam liber tempor cum soluta nobis eleifend option congue nihil imperdiet doming id quod mazim placerat facer possim assum. Typi non habent claritatem insitam;</p>
      <p>Est usus legentis in iis qui facit eorum claritatem.</p>
      <p>Investigationes demonstraverunt lectores legere me lius quod ii legunt saepius. Claritas est etiam processus dynamicus, qui sequitur mutationem consuetudium lectorum. Mirum est notare quam littera gothica, quam nunc putamus parum claram, anteposuerit litterarum formas humanitatis per seacula quarta decima et quinta decima. Eodem modo typi, qui nunc nobis videntur parum clari, fiant sollemnes in futurum.</p>
      <p>Consectetuer adipiscing elit, sed diam nonummy nibh euismod tincidunt ut laoreet dolore magna aliquam erat volutpat. Ut wisi enim ad minim veniam, quis nostrud exerci tation ullamcorper suscipit lobortis nisl ut aliquip ex ea commodo consequat. Duis autem vel eum iriure dolor in hendrerit in vulputate velit esse molestie consequat, vel illum dolore eu feugiat nulla facilisis at vero eros et accumsan et iusto odio dignissim qui blandit praesent luptatum zzril delenit augue duis dolore te feugait nulla facilisi.</p>
      <p>Nam liber tempor cum soluta nobis eleifend option congue nihil imperdiet.</p>
    </div>
    <div class="abs lh-signature" role="img" aria-label="Handwritten signature of the sender"></div>
    <div class="abs lh-signer">Alan Brooks</div>
    <div class="abs lh-signer-role">Managing Director</div>
  </section>

  <section class="piece env-large" aria-label="10 x 13 mailing envelope">
    <div class="abs brand-name">VALE 8</div>
    <div class="abs brand-tag">CPAS and Tax Advisors</div>
    <div class="abs small-addr">Your address, city<br>state, ZIP 0000</div>
  </section>

  <section class="piece env-medium" aria-label="9 x 12 mailing envelope">
    <div class="abs brand-name">VALE 8</div>
    <div class="abs brand-tag">CPAS and Tax Advisors</div>
    <div class="abs small-addr">Your address, city<br>state, ZIP 0000</div>
  </section>

  <section class="piece env-business" aria-label="9.5 x 4.125 envelope front">
    <div class="abs brand-name">VALE 8</div>
    <div class="abs brand-tag">CPAS and Tax Advisors</div>
    <div class="abs small-addr">Your address, city<br>state, ZIP 0000</div>
  </section>

  <section class="piece env-back" aria-label="9.5 x 4.125 envelope back">
    <svg class="env-flap" viewBox="0 0 387 50" aria-hidden="true">
      <path d="M1 0 L8 30 Q12 46 32 46 L355 46 Q375 46 379 30 L386 0 Z" fill="#fff" stroke="rgba(0,0,0,.12)" stroke-width="1"/>
    </svg>
    <div class="abs brand-name">VALE 8</div>
    <div class="abs brand-tag">CPAS and Tax Advisors</div>
  </section>

</main>
</body>
</html>
```